Harlow Vale Boxing Gym's Fennick Trim-Up Contest

Harlow Vale Boxing Gym Presents
“The Fennick Trim-Up Challenge”
Win the fight for fitness and take home awesome prizes.
1st Place Tavlo Mini (16gb) (value $299)
2nd Place One-Month All Access Membership (value $199)
3rd Place Harlow Vale Boxing Gym Training Gloves, T-Shirt and Handwraps (value $79)
(fine print)
* Men’s & Women’s Divisions – two sets of prizes.
* Contestants must register between June 10th and June 15th. Entry fee is $25.
* At registration, contestants will be required to weigh-in in a private setting. For the duration of the competition, actual weight will not be posted; only percent gain or loss.
* Results are based on percentage weight loss as measured on September 19th.
Note: Harlow Vale Boxing Gym reserves the right to cancel the competition in a division if there are fewer than 10 contestants in that division. In that event, a full refund will be issued to participants in that division.

ABOUT US:
HVBG is not a traditional health club with rows of cardio equipment, weight-training machines, or overcrowded step-aerobic classes. Nor are we like old-school boxing or martial arts studios which can oftentimes be scary and uninviting.

Our goal is to strike a balance between instruction, conditioning and fun. We offer over 70 classes per week: mostly boxing, but also muay thai, mixed martial arts ("MMA"), and boot camps. All of our instructors have fought professionally or at the amateur level so they're teaching from experience, not what they learned from an online course.

Target Market(s)

Gym members.

Industry/Entity Type

Fitness

Requirements
Must have
• Our logo (attached) converted to blue.

```html
<!DOCTYPE html>
<html lang="en">
<head>
<meta charset="utf-8">
<title>Harlow Vale Boxing Gym – The Fennick Trim-Up Challenge</title>
<link rel="stylesheet" href="https://fonts.googleapis.com/css2?family=Roboto+Condensed:wght@100;200;800;900&family=Exo:wght@500;600&family=Arimo:wght@400;700&display=swap">
<style>
  :root {
    --navy: #22305f;
    --cream: #fdf2bf;
    --peach: #fbc57a;
    --orange: #f39a4c;
    --page: #ffffff;
  }
  * { margin: 0; padding: 0; box-sizing: border-box; }
  html, body { width: 1200px; height: 900px; overflow: hidden; background: var(--page); }
  .canvas { position: relative; width: 1200px; height: 900px; }
  .poster {
    position: absolute; left: 245px; top: 0; width: 710px; height: 900px;
    overflow: hidden; color: var(--navy);
    background: var(--cream);
  }
  .poster-glow { position: absolute; inset: 0; width: 100%; height: 100%; }
  .content { position: absolute; inset: 0; }

  .brand {
    position: absolute; top: 50px; left: 0; width: 100%;
    display: flex; justify-content: center; align-items: center; gap: 8px;
    font-family: "Exo", sans-serif; font-weight: 600; font-size: 18px; color: var(--navy);
  }
  .brand-mark { width: 12px; height: 12px; background: var(--navy); }

  .presents {
    position: absolute; top: 100px; width: 100%; text-align: center;
    font-family: "Exo", sans-serif; font-weight: 500; font-size: 21px; letter-spacing: 0.3px;
  }

  .headline { font-family: "Roboto Condensed", sans-serif; text-align: center; position: absolute; width: 100%; line-height: 1; }
  .headline-top { top: 145px; font-weight: 900; font-size: 112px; letter-spacing: -1px; }
  .headline-middle { top: 250px; font-weight: 100; font-size: 152px; letter-spacing: -2px; }
  .headline-bottom { top: 382px; font-weight: 900; font-size: 130px; letter-spacing: -1px; }

  .tagline {
    position: absolute; top: 532px; width: 100%; text-align: center;
    font-family: "Exo", sans-serif; font-weight: 500; font-size: 31px; line-height: 36px;
    letter-spacing: 1px;
  }

  .prizes { position: absolute; top: 627px; left: 88px; right: 20px; list-style: none; }
  .prize { display: flex; align-items: baseline; margin-bottom: 6px; }
  .prize-rank {
    font-family: "Roboto Condensed", sans-serif; font-weight: 800; font-size: 21px;
    width: 99px; flex: none; white-space: nowrap; line-height: 24px;
  }
  .prize-item { font-family: "Exo", sans-serif; font-weight: 500; font-size: 16.5px; line-height: 24px; letter-spacing: 0.3px; }

  .fine-print {
    position: absolute; top: 774px; left: 40px; right: 40px;
    font-family: "Arimo", sans-serif; font-weight: 700; font-size: 9.5px; line-height: 12px;
    list-style: none;
  }
  .fine-print li { padding-left: 7px; text-indent: -7px; }
  .fine-print li::before { content: "* "; }
  .note {
    position: absolute; top: 840px; left: 48px; right: 40px;
    font-family: "Arimo", sans-serif; font-weight: 700; font-size: 9.5px; line-height: 12px;
  }
</style>
</head>
<body>
<div class="canvas">
  <div class="poster">
    <svg class="poster-glow" viewBox="0 0 710 900" preserveAspectRatio="none" aria-hidden="true">
      <defs>
        <linearGradient id="edge-left" x1="0" y1="0" x2="1" y2="0">
          <stop offset="0" stop-color="#f39a4c"/>
          <stop offset="0.6" stop-color="#f5a458"/>
          <stop offset="1" stop-color="#fbc57a" stop-opacity="0.6"/>
        </linearGradient>
        <linearGradient id="edge-right" x1="1" y1="0" x2="0" y2="0">
          <stop offset="0" stop-color="#f39a4c"/>
          <stop offset="0.6" stop-color="#f5a458"/>
          <stop offset="1" stop-color="#fbc57a" stop-opacity="0.6"/>
        </linearGradient>
        <radialGradient id="centre-glow" cx="0.5" cy="0.5" r="0.5">
          <stop offset="0" stop-color="#fdf2bf"/>
          <stop offset="0.7" stop-color="#fdf2bf" stop-opacity="0.7"/>
          <stop offset="1" stop-color="#fdf2bf" stop-opacity="0"/>
        </radialGradient>
        <linearGradient id="bottom-fade" x1="0" y1="0" x2="0" y2="1">
          <stop offset="0" stop-color="#fdf2bf" stop-opacity="0"/>
          <stop offset="1" stop-color="#fdf2bf" stop-opacity="0.85"/>
        </linearGradient>
      </defs>
      <rect width="710" height="900" fill="#fbd996"/>
      <ellipse cx="-40" cy="430" rx="190" ry="700" fill="url(#edge-left)"/>
      <ellipse cx="750" cy="430" rx="190" ry="700" fill="url(#edge-right)"/>
      <ellipse cx="355" cy="420" rx="300" ry="620" fill="url(#centre-glow)"/>
      <rect y="560" width="710" height="340" fill="url(#bottom-fade)"/>
    </svg>

    <div class="content">
      <div class="brand"><span class="brand-mark"></span>Harlow Vale Boxing</div>
      <p class="presents">Harlow Vale Boxing Gym Presents</p>

      <h1>
        <span class="headline headline-top">THE FENNICK</span>
        <span class="headline headline-middle">TRIM-UP</span>
        <span class="headline headline-bottom">CHALLENGE</span>
      </h1>

      <p class="tagline">Win the fight for fitness and take<br>home awesome prizes!</p>

      <ul class="prizes">
        <li class="prize"><span class="prize-rank">1st Place</span><span class="prize-item">Tavlo Mini (16gb) (value $299)</span></li>
        <li class="prize"><span class="prize-rank">2nd Place</span><span class="prize-item">One-Month All Access Membership (value $199)</span></li>
        <li class="prize"><span class="prize-rank">3rd Place</span><span class="prize-item">Harlow Vale Boxing Gym Training Gloves,<br>T-Shirt and Handwraps (value $79)</span></li>
      </ul>

      <ul class="fine-print">
        <li>Men’s &amp; Women’s Divisions – two sets of prizes.</li>
        <li>Contestants must register between June 10th and June 15th. Entry fee is $25.</li>
        <li>At registration, contestants will be required to weigh-in in a private setting. For the duration of the competition, actual weight will not be posted; only percent gain or loss.</li>
        <li>Results are based on percentage weight loss as measured on September 19th.</li>
      </ul>
      <p class="note">Note: Harlow Vale Boxing Gym reserves the right to cancel the competition in a division if there are fewer than 10 contestants in that division. In that event, a full refund will be issued to participants in that division.</p>
    </div>
  </div>
</div>
</body>
</html>
```